Business card for Luxury Portable Restroom Trailer company

We are a Luxury Portable Restroom Trailer Company Called FALCRIDGE HIRES. Based in Orange County California. We provide portable restroom trailers for events, such as, Weddings, Concerts, Charity events, Sporting events, Tournaments, Corporate events, ect. We rent and Sell the Luxury restrooms. Our colors are white, grey, and Orange. As you will see in the logo we uploaded.
There are 2 people in the company so the names and titles will change for the 3 people but card will remain the same. Here is the information for each Person: Dwight Penner CFO 555 318-0476
next Person: Leon Marchetti VP 555 318-0476
Next Person: Owen Marchetti CEO 555 318-0476
Information to include on the card: Luxury Restroom Trailers Rental and Sales. Weddings, Concerts, Charity, Sporting and Corp. Events.

```html
<!DOCTYPE html>
<html lang="en">
<head>
<meta charset="UTF-8">
<title>FALCRIDGE HIRES – Business Card</title>
<link rel="stylesheet" href="https://fonts.googleapis.com/css2?family=Montserrat:wght@400;500;700;800&display=swap">
<style>
  :root {
    --page-bg: #d6d6d6;
    --card-white: #ededed;
    --grey-dark: #525253;
    --grey-light: #8c8c8c;
    --orange: #e0601f;
    --orange-light: #e98c5c;
    --white: #ffffff;
  }
  * { box-sizing: border-box; margin: 0; padding: 0; }
  html, body {
    width: 1200px; height: 1200px; overflow: hidden;
    background: var(--page-bg);
    font-family: "Montserrat", sans-serif;
  }
  .stage {
    position: relative; width: 1200px; height: 1200px;
  }
  .card {
    position: absolute; left: 250px; width: 700px; height: 400px;
    border-radius: 22px; overflow: hidden;
    box-shadow: 0 6px 18px rgba(0,0,0,0.18);
  }
  /* Front */
  .card-front {
    top: 150px;
    background: linear-gradient(100deg, var(--grey-light) 0%, var(--grey-dark) 60%, var(--grey-dark) 100%);
    display: flex; align-items: center; justify-content: center;
  }
  .front-name {
    color: var(--white); font-weight: 800; font-size: 56px;
    letter-spacing: 2px;
  }
  /* Back */
  .card-back { top: 650px; background: var(--card-white); }
  .brand-mark {
    position: absolute; top: 50px; left: 0; width: 100%;
    display: flex; align-items: center; justify-content: center; gap: 14px;
  }
  .brand-dot {
    width: 34px; height: 34px; border-radius: 50%;
    border: 5px solid var(--orange);
  }
  .brand-name {
    color: var(--orange); font-weight: 800; font-size: 30px; letter-spacing: 1px;
  }
  .contact-panel {
    position: absolute; left: 0; top: 195px; width: 385px; height: 185px;
    background: linear-gradient(90deg, var(--orange-light) 0%, var(--orange) 100%);
    color: var(--white); padding: 26px 0 0 58px;
  }
  .person-name { font-weight: 700; font-size: 30px; line-height: 1; }
  .person-title { font-weight: 400; font-size: 18px; margin: 6px 0 16px 12px; }
  .contact-list { list-style: none; margin-left: 24px; }
  .contact-list li {
    display: flex; align-items: center; gap: 10px;
    font-size: 16px; font-weight: 500; line-height: 26px;
  }
  .contact-list svg { width: 16px; height: 16px; flex: none; }
  .services-panel {
    position: absolute; left: 395px; top: 140px; width: 305px; height: 200px;
    background: var(--grey-dark); color: var(--white);
    padding: 16px 0 0 40px;
  }
  .services-list { list-style: disc; padding-left: 16px; }
  .services-list li { font-size: 16px; line-height: 28px; }
</style>
</head>
<body>
<div class="stage">
  <section class="card card-front">
    <div class="front-name">FALCRIDGE HIRES</div>
  </section>

  <section class="card card-back">
    <div class="brand-mark">
      <span class="brand-dot"></span>
      <span class="brand-name">FALCRIDGE HIRES</span>
    </div>

    <div class="contact-panel">
      <div class="person-name">Dwight Penner</div>
      <div class="person-title">CFO</div>
      <ul class="contact-list">
        <li>
          <svg viewBox="0 0 16 16" fill="#fff"><path d="M3.6 1.5l2.3 2.6-1.3 1.7c.9 2 2.5 3.6 4.6 4.6l1.7-1.3 2.6 2.3-1.2 2.3C7 13.5 2.5 9 1.3 2.7z"/></svg>
          555 318-0476
        </li>
        <li>
          <svg viewBox="0 0 16 16" fill="#fff"><path d="M1 3h14v10H1z M2 4l6 5 6-5" stroke="#e0601f" stroke-width="1.2"/></svg>
          info@falcridgehires.com
        </li>
        <li>
          <svg viewBox="0 0 16 16" fill="none" stroke="#fff" stroke-width="1.4"><circle cx="8" cy="8" r="6.5"/><path d="M1.5 8h13M8 1.5c-3 3.5-3 9.5 0 13M8 1.5c3 3.5 3 9.5 0 13"/></svg>
          www.falcridgehires.com
        </li>
      </ul>
    </div>

    <div class="services-panel">
      <ul class="services-list">
        <li>Luxury Restroom</li>
        <li>Trailers Rental and Sales</li>
        <li>Weddings</li>
        <li>Concerts</li>
        <li>Charity</li>
        <li>Sporting and Corp. Events</li>
      </ul>
    </div>
  </section>
</div>
</body>
</html>
```